Business Cards for IT Consulting Company (Managed Service Provider)

I am looking to have some business cards printed and would like some designs. We are an IT Consulting company based in Vancouver BC. I would like a nice clean and modern look to the cards. I have uploaded all the versions of my logo so parts can be used as needed. Here is a snippit from our website homepage:

Quillbrook Networks Ltd. is an IT Solutions Partner located in Vancouver BC, Canada. We offer IT solutions and support to customers in the greater Vancouver Area. With expertise in Microsoft platforms, as well as Linux and Mac OSX and over 12 years experience in the IT industry, Quillbrook Networks is dedicated to offering our clients top quality service and products. We take pride in the solutions we offer our customers. The greatest compliment a client can give us is to recommend our services.

Quillbrook Networks Ltd. offers a wide range of IT services from onsite service to remote support and managed service solutions. This allows clients to choose the support path that best suits their company’s needs. Supporting many different sized companies from small to enterprise level over the past 12 years Quillbrook Networks has the experience and expertise needed to ensure things run smoothly. Allowing our clients to focus on doing business.

Revolutionizing the way IT services are delivered.

Quillbrook Networks is dedicated to providing our clients with IT solutions that work and grow with them for years to come. This philosophy helps save money in the long run instead of replacing equipment constantly. Far too often IT solutions are not well thought out and while possibly solving the problem at hand, require replacement due to growth or quality within a very short time frame. Quillbrook Networks takes pride in providing solutions that will last and be able to accommodate growth without the need for replacement.

Industry/Entity Type

Information Technology

Contact Information for Business Card

Quillbrook Networks Ltd.
(Employee Name)
Eml: (Employees Email Address)
Web: quillbrook.me
Ph: 604-555-0148

Font styles to use
Serif
Sans Serif

Requirements
Must have
• The Company logo and company colors.
Nice to have
• - Our tag line: "Revolutionizing IT Services" or "Revolutionizing the way IT services are delivered."
• - Also I really like the idea of nature and technology together blending which is sort of where my logo came from so integrating that somehow onto the business cards would be great.

```html
<!DOCTYPE html>
<html lang="en">
<head>
<meta charset="utf-8">
<title>Quillbrook Networks Ltd. — Business Cards</title>
<link rel="stylesheet" href="https://fonts.googleapis.com/css2?family=Roboto:ital,wght@0,400;0,500;0,700;1,400&display=swap">
<style>
  :root {
    --bg: #a3a2a2;
    --card-dark: #1f1f20;
    --card-light: #f1f1f1;
    --brand-blue: #1a8fd6;
    --brand-grey: #4a4a4b;
    --text-dark: #3a3a3a;
    --text-light: #f4f4f4;
  }
  * { margin: 0; padding: 0; box-sizing: border-box; }
  html, body { width: 1200px; height: 1200px; overflow: hidden; }
  body {
    background: var(--bg);
    font-family: "Roboto", Arial, sans-serif;
    position: relative;
  }
  .card { position: absolute; overflow: hidden; }

  /* Front card */
  .card-front {
    left: 238px; top: 117px; width: 713px; height: 420px;
    background: var(--card-dark);
  }
  .brand {
    position: absolute;
    display: flex; align-items: center; gap: 16px;
    color: var(--brand-blue);
    font-weight: 500;
    white-space: nowrap;
  }
  .brand-dot {
    border-radius: 50%;
    border: 4px solid var(--brand-blue);
    flex: none;
  }
  .card-front .brand { left: 110px; top: 150px; font-size: 44px; }
  .card-front .brand-dot { width: 60px; height: 60px; }
  .front-tagline {
    position: absolute; left: 0; right: 0; top: 376px;
    display: flex; justify-content: center; align-items: center; gap: 16px;
    color: var(--text-light); font-size: 18px; letter-spacing: 0.2px;
  }
  .front-tagline .rule {
    width: 110px; height: 3px;
    background: linear-gradient(to right, transparent, var(--brand-blue) 25%, var(--brand-blue) 75%, transparent);
  }

  /* Back card */
  .card-back {
    left: 231px; top: 643px; width: 712px; height: 418px;
    background: var(--card-light);
  }
  .wave { position: absolute; left: 0; top: 0; }
  .back-tagline {
    position: absolute; right: 38px; top: 30px;
    text-align: right; color: var(--text-light);
    font-size: 18px; line-height: 25px;
  }
  .card-back .brand { left: 34px; top: 150px; font-size: 40px; }
  .card-back .brand-dot { width: 52px; height: 52px; }
  .contact-list {
    position: absolute; left: 52px; top: 288px;
    list-style: none; color: var(--text-dark); font-size: 18px;
  }
  .contact-list li { display: flex; align-items: center; gap: 16px; height: 27.5px; }
  .contact-list svg { width: 16px; height: 16px; fill: var(--brand-blue); flex: none; }
  .person { position: absolute; right: 38px; top: 305px; text-align: right; }
  .person-name { color: var(--brand-blue); font-size: 26px; font-weight: 700; }
  .person-role { color: var(--text-dark); font-size: 17px; font-style: italic; margin-top: 4px; }
</style>
</head>
<body>

<section class="card card-front" aria-label="Card front">
  <div class="brand"><span class="brand-dot"></span>Quillbrook Networks Ltd.</div>
  <div class="front-tagline">
    <span class="rule"></span>
    <span>Revolutionizing IT Services</span>
    <span class="rule"></span>
  </div>
</section>

<section class="card card-back" aria-label="Card back">
  <svg class="wave" width="712" height="418" viewBox="0 0 712 418" aria-hidden="true">
    <path d="M0 0 H712 V165 C600 165 520 122 430 82 C330 38 150 28 0 46 Z" fill="var(--brand-blue)"/>
    <path d="M0 46 C150 28 330 38 430 82 C520 122 600 165 712 165 V178 C590 178 510 142 420 102 C320 60 150 52 0 64 Z" fill="var(--brand-grey)"/>
    <path d="M60 58 C200 30 390 30 470 62 C380 44 220 44 60 58 Z" fill="var(--brand-grey)"/>
  </svg>

  <p class="back-tagline">Revolutionizing the<br>way IT services<br>are delivered</p>

  <div class="brand"><span class="brand-dot"></span>Quillbrook Networks Ltd.</div>

  <ul class="contact-list">
    <li>
      <svg viewBox="0 0 16 16"><path d="M3 2 L6 2 L7 5 L5 6.5 C6 8.5 7.5 10 9.5 11 L11 9 L14 10 L14 13 C14 13.6 13.6 14 13 14 C7 14 2 9 2 3 C2 2.4 2.4 2 3 2 Z"/></svg>
      604-555-0148
    </li>
    <li>
      <svg viewBox="0 0 16 16"><path d="M8 1a7 7 0 1 0 0 14A7 7 0 0 0 8 1Zm0 1.5c.8 0 1.8 1.6 2.1 4H5.9C6.2 4.1 7.2 2.5 8 2.5ZM2.6 7.5h1.8c0-1.4.3-2.8.8-3.9A5.5 5.5 0 0 0 2.6 7.5Zm0 1h1.8c.1 1.4.3 2.8.8 3.9a5.5 5.5 0 0 1-2.6-3.9Zm3.3 0h4.2c-.3 2.4-1.3 4-2.1 4s-1.8-1.6-2.1-4Zm5.7-1h1.8a5.5 5.5 0 0 0-2.6-3.9c.5 1.1.8 2.5.8 3.9Zm0 1h1.8a5.5 5.5 0 0 1-2.6 3.9c.5-1.1.7-2.5.8-3.9Z"/></svg>
      www.quillbrook.me
    </li>
    <li>
      <svg viewBox="0 0 16 16"><path d="M1 3h14v10H1Z M2 4l6 5 6-5" fill="var(--brand-blue)"/><path d="M1.5 3.5 8 9l6.5-5.5" fill="none" stroke="var(--card-light)" stroke-width="1.2"/></svg>
      support@quillbrook.me
    </li>
  </ul>

  <div class="person">
    <div class="person-name">Daniel Moreau</div>
    <div class="person-role">Managing Director</div>
  </div>
</section>

</body>
</html>
```